RW Holloway LLC Business Card - Civil Engineering & Consulting Firm

We need a Business Card that is elegant, and masculine.  It is our Professional Civil Engineering & Consulting Company located in San Antonio TX (Not s construction or builder firm- no gears & no tool images please). We provide civil engineering services including  commercial site plans, grading and drainage plans, utility plans, hydraulics and hydrology, land planning, utility coordination, and other general civil engineering services related to commercial and residential development.
We have 2 existing Logos. We would like to convey reliability, strength, trustworthiness and attention to detail.  Blues and orange tones as per logo We are OK with the use of a darker blue in the mix.  We have 2 logo versions - Full Company Name Logo to go on the back of card, & Small Icon Logo for the front w/ personal Info.

Target Market(s)
Architects, Real Estate Developers, Other Strctural Engineers, Surveyers, General Contractors
Industry/Entity Type
Professional Civil Engineering
Contact Information for Business Card
Name, Position, Address, Cell & Office #, email, and company website
Font styles to use
Other font styles liked:
- Avian
Requirements
Should not have
- No Tools, No Gears, no Cranes, or Construction Equipment.

```html
<!DOCTYPE html>
<html lang="en">
<head>
<meta charset="utf-8">
<title>RW Holloway LLC — Business Card</title>
<link rel="stylesheet" href="https://fonts.googleapis.com/css2?family=Montserrat:wght@400;500;700&family=Josefin+Sans:wght@300;400&display=swap">
<style>
  :root {
    --backdrop: #3b3b3b;
    --card: #161616;
    --edge-blue: #6fa3d8;
    --brand-blue: #6aa6dc;
    --brand-orange: #e8912c;
    --text-light: #e9e9e9;
    --rule: #4b5d72;
    --mark-grey: #9a9a9a;
  }
  * { box-sizing: border-box; margin: 0; padding: 0; }
  html, body {
    width: 1200px; height: 801px; overflow: hidden;
    background: var(--backdrop);
    font-family: "Montserrat", sans-serif;
  }
  .sheet {
    position: relative; width: 1200px; height: 801px;
    display: flex; align-items: center; justify-content: center; gap: 40px;
  }
  .card {
    position: relative; width: 520px; height: 297px;
    background: var(--card);
    border-bottom: 2px solid var(--edge-blue);
    border-left: 1px solid rgba(111,163,216,0.35);
    box-shadow: 0 10px 24px rgba(0,0,0,0.35);
  }
  /* Front */
  .brand {
    position: absolute; top: 48px; left: 0; right: 0;
    text-align: center;
  }
  .brand-name {
    display: inline-flex; align-items: center; gap: 10px;
    font-family: "Josefin Sans", sans-serif; font-weight: 300;
    font-size: 34px; letter-spacing: 3px; color: var(--brand-blue);
  }
  .brand-square {
    width: 14px; height: 14px; background: var(--brand-orange);
  }
  .brand-rule {
    width: 250px; height: 1px; margin: 8px auto 6px;
    background: var(--brand-blue);
  }
  .brand-tagline {
    font-family: "Josefin Sans", sans-serif; font-weight: 400;
    font-size: 10px; letter-spacing: 4px; color: var(--brand-orange);
  }
  .details {
    position: absolute; left: 0; right: 0; top: 160px;
    display: flex; justify-content: center; align-items: center; gap: 22px;
  }
  .person { text-align: right; }
  .person-name {
    font-weight: 700; font-size: 17px; color: var(--brand-blue); letter-spacing: 0.3px;
  }
  .person-role {
    font-weight: 500; font-size: 12px; color: var(--brand-orange); margin: 2px 0 8px;
  }
  .person-address {
    font-size: 11.5px; color: var(--text-light); line-height: 1.45;
  }
  .divider { width: 1px; height: 84px; background: var(--rule); }
  .contacts { list-style: none; }
  .contacts li {
    display: flex; align-items: center; gap: 7px;
    font-size: 11.5px; color: var(--text-light); line-height: 1.55;
  }
  .contacts svg { width: 10px; height: 10px; fill: var(--brand-orange); flex: none; }
  /* Back */
  .back-mark {
    position: absolute; inset: 0;
    display: flex; align-items: center; justify-content: center; gap: 12px;
    font-family: "Josefin Sans", sans-serif; font-weight: 300;
    font-size: 30px; letter-spacing: 4px; color: var(--mark-grey);
  }
  .back-square { width: 14px; height: 14px; background: var(--mark-grey); }
</style>
</head>
<body>
<main class="sheet">
  <section class="card card-front" aria-label="Front of card">
    <div class="brand">
      <div class="brand-name"><span class="brand-square"></span>RW HOLLOWAY LLC</div>
      <div class="brand-rule"></div>
      <div class="brand-tagline">CONSULTING ENGINEERS</div>
    </div>
    <div class="details">
      <div class="person">
        <div class="person-name">DANIEL HARROW</div>
        <div class="person-role">President</div>
        <div class="person-address">1180 Alamo Ridge Drive<br>San Antonio TX 78209</div>
      </div>
      <div class="divider"></div>
      <ul class="contacts">
        <li><svg viewBox="0 0 10 10"><rect x="2" y="0" width="6" height="10" rx="1"/><rect x="3" y="1.5" width="4" height="6" fill="#161616"/></svg>555-318-7402</li>
        <li><svg viewBox="0 0 10 10"><path d="M1 2 Q1 0 3 1 L4 3 L3 4 Q4 6 6 7 L7 6 L9 7 Q10 9 8 9 Q2 8 1 2Z"/></svg>555-318-7410</li>
        <li><svg viewBox="0 0 10 10"><rect x="0" y="2" width="10" height="7"/><path d="M0 2 L5 6 L10 2" stroke="#161616" stroke-width="1" fill="none"/></svg>info@rwhollowayllc.com</li>
        <li><svg viewBox="0 0 10 10"><circle cx="5" cy="5" r="5"/><path d="M0 5 H10 M5 0 V10" stroke="#161616" stroke-width="0.8"/></svg>www.rwhollowayllc.com</li>
      </ul>
    </div>
  </section>
  <section class="card card-back" aria-label="Back of card">
    <div class="back-mark"><span class="back-square"></span>RW HOLLOWAY LLC</div>
  </section>
</main>
</body>
</html>
```